WEBSITE & LOGO for MEDICAL CILINC

BRAND NAME ( LUMORA) Medical clinic for intravenous (IV) vitamin hydration and wellness therapy. range of signature infusions and boosters are targeted at preventative health and wellness – essentially replenishing your body with the fluids and vitamins it needs to be in tip-top condition.

Blood testing
laboratory analysis
IV therapy
IV infusion drips
phlebotomy services
nurses for Home care services
Patient repatriation services to their countries
Hire of medical equipments including beds and wheel chairs

www.quellsa.com
www.tovexclinic.com
http://pickaflask.co.uk

All adults
18+ women and men.

No black color in the background
DNA double helix image should to be implemented in the design and logo.
the website should be easy to be used so the clients can add to the shopping cart
- select treatment or drips
- supplement
- book nurses
- book home visit
- book nurse for international home care journey

Colors
86cae7
33b8a4
e4daeb
f9d9e8
fefafc
fbd2d3
eee9f4
85acd3
0455a3

Requirements
Must have
• DNA Double helix in Java animation
injection icon for IV injection
Infusion Icon Bag for IV infusion
Analysis icon
phlebotomy services icon
Patient repatriation services icon
Hire of medical equipments icon

light background and water blue menu and buttons with highlights
Nice to have
• dynamic website where
IV injections scroll from side to side
IV infusion scroll from side to side.

```html
<!DOCTYPE html>
<html lang="en">
<head>
<meta charset="utf-8">
<title>Lumora — IV Vitamin Hydration &amp; Wellness Clinic</title>
<link rel="stylesheet" href="https://fonts.googleapis.com/css2?family=Rubik:ital,wght@0,300;0,400;0,500;0,600;1,400&family=Lora:wght@700&display=swap">
<style>
:root{
  --navy:#0f4d9e;
  --deep:#0455a3;
  --teal:#33b8a4;
  --water:#86cae7;
  --ink:#333a40;
  --grey:#6c6c6c;
  --pink:#f9eff3;
  --lavender:#ebe3ef;
  --white:#ffffff;
  --line:#e8e8e8;
}
*{box-sizing:border-box;margin:0;padding:0}
html,body{width:1200px;height:4706px;overflow:hidden;background:var(--white)}
body{font-family:"Rubik",sans-serif;color:var(--ink);position:relative}
.abs{position:absolute}
.btn{position:absolute;display:flex;align-items:center;justify-content:center;text-align:center;color:var(--white);font-weight:500;border-radius:40px;line-height:1.2}
.btn--teal{background:var(--teal)}
.btn--navy{background:var(--navy)}
.section-title{position:absolute;left:0;width:1200px;text-align:center;font-weight:500;font-size:40px;color:var(--ink)}
.body-copy{font-size:14.5px;line-height:24.6px;color:var(--grey);font-weight:300}

/* header */
.site-header{position:absolute;left:0;top:0;width:1200px;height:140px;border-bottom:1px solid var(--line)}
.phone{left:170px;top:24px;display:flex;align-items:center;gap:10px;font-size:15px;color:var(--navy)}
.brand{left:502px;top:16px;display:flex;align-items:center;gap:10px;font-size:36px;font-weight:600;color:var(--deep);letter-spacing:1px}
.brand-dot{width:16px;height:16px;border-radius:50%;background:var(--teal)}
.site-header .btn{top:20px;height:34px;font-size:14px;font-weight:400}
.main-nav{left:0;top:94px;width:1200px;height:20px;font-size:15px;font-weight:500;color:var(--navy)}
.main-nav span{position:absolute;transform:translateX(-50%);white-space:nowrap}
.main-nav .active{color:var(--teal)}
.header-icons{left:958px;top:86px;display:flex;gap:18px}
.cart-badge{position:absolute;left:52px;top:-4px;width:11px;height:11px;border-radius:50%;background:#f25c54}

/* hero */
.hero{left:0;top:140px;width:1200px;height:632px;overflow:hidden;
  background:
    radial-gradient(ellipse 520px 700px at 330px 300px,rgba(20,90,210,.85) 0%,rgba(10,50,150,.5) 45%,transparent 75%),
    linear-gradient(100deg,#0a2a86 0%,#071f6a 40%,#04123f 70%,#020a2c 100%)}
.hero-visual{left:150px;top:-20px;width:420px;height:680px;
  background:
    radial-gradient(ellipse 90px 120px at 150px 90px,rgba(120,230,255,.55),transparent 70%),
    radial-gradient(ellipse 120px 110px at 230px 250px,rgba(90,210,255,.6),transparent 70%),
    radial-gradient(ellipse 110px 120px at 170px 420px,rgba(80,200,255,.5),transparent 70%),
    radial-gradient(ellipse 100px 120px at 250px 580px,rgba(70,190,250,.45),transparent 70%),
    radial-gradient(ellipse 200px 340px at 200px 340px,rgba(40,140,240,.35),transparent 75%)}
.hero-title{left:690px;top:180px;font-size:88px;font-weight:500;color:var(--white);letter-spacing:2px}
.hero-sub{left:696px;top:286px;font-size:17px;line-height:25px;color:var(--white)}
.hero .btn{left:694px;top:354px;width:184px;height:52px;font-size:16px}

/* services */
.service-card{position:absolute;width:203px;height:190px}
.service-card svg{position:absolute;left:71px;top:44px}
.service-label{position:absolute;left:14px;right:14px;top:151px;background:var(--white);padding:10px 6px 0;text-align:center;font-size:12.5px;line-height:16px;color:var(--ink);min-height:39px}
.tone-a{background:linear-gradient(150deg,#8e9aa3 0%,#5e6b76 50%,#7f8a93 100%)}
.tone-b{background:linear-gradient(150deg,#6f7880 0%,#3f4952 55%,#5b666f 100%)}
.tone-c{background:linear-gradient(150deg,#9aa6b0 0%,#66747f 50%,#8895a0 100%)}
.tone-d{background:linear-gradient(150deg,#7c8a80 0%,#56625c 50%,#7b8680 100%)}

/* about */
.about-photo{left:0;top:1474px;width:599px;height:564px;
  background:
    radial-gradient(ellipse 160px 140px at 440px 110px,rgba(150,110,90,.55),transparent 70%),
    radial-gradient(ellipse 160px 60px at 190px 220px,rgba(110,170,210,.55),transparent 70%),
    linear-gradient(135deg,#f3f4f6 0%,#e7e9ec 45%,#d5d9de 100%)}
.about-panel{left:599px;top:1474px;width:601px;height:564px;background:var(--pink)}
.about-panel h2{position:absolute;left:49px;top:86px;font-size:40px;font-weight:500}
.about-panel .body-copy{position:absolute;left:49px;top:152px;width:440px}
.about-panel .btn{left:49px;top:418px;width:270px;height:66px;font-size:15px}

/* supplements */
.supp{position:absolute;width:260px;text-align:center}
.supp-visual{margin:0 auto;width:200px;height:146px}
.supp h3{margin-top:28px;font-size:18px;font-weight:500}
.supp p{margin-top:14px;font-size:14px;line-height:24.5px;color:var(--grey);font-weight:300}

/* future */
.future-panel{left:0;top:2681px;width:583px;height:584px;background:var(--lavender)}
.future-panel h2{position:absolute;left:142px;top:102px;font-size:40px;line-height:40px;font-weight:500}
.future-panel .body-copy{position:absolute;left:142px;top:198px;width:410px}
.future-panel .btn{left:142px;top:460px;width:198px;height:56px;font-size:16px}
.future-photo{left:583px;top:2681px;width:617px;height:584px;
  background:
    radial-gradient(ellipse 140px 110px at 250px 210px,rgba(230,245,255,.75),transparent 70%),
    radial-gradient(ellipse 260px 400px at 500px 300px,rgba(235,240,246,.9),transparent 70%),
    linear-gradient(110deg,#0d3a5e 0%,#1c6b8f 35%,#5aa3c4 60%,#cfdde7 85%,#eef2f5 100%)}

/* vitamin */
.hex{left:150px;top:3333px}
.vitamin h2{position:absolute;left:617px;top:3408px;font-size:40px;font-weight:500}
.vitamin .body-copy{position:absolute;left:617px;top:3472px;width:420px}
.vitamin .btn{left:617px;top:3711px;width:138px;height:54px;font-size:16px}

/* testimonials */
.testimonials{left:0;top:3910px;width:1200px;height:482px;background:radial-gradient(ellipse at 50% 40%,#1e63c4 0%,#0d4aa8 55%,#0a3f93 100%)}
.testimonials h2{position:absolute;left:0;top:64px;width:1200px;text-align:center;color:var(--white);font-size:44px;font-weight:500}
.quote-card{position:absolute;top:147px;width:278px;height:240px;border:2px solid rgba(255,255,255,.7);color:var(--white);padding:40px 22px 0;background:rgba(6,40,110,.35)}
.quote-card p{margin-top:14px;font-size:11.5px;line-height:21px;font-style:italic}
.quote-card cite{display:block;margin-top:14px;font-family:"Lora",serif;font-weight:700;font-size:17px;font-style:normal}

/* footer */
.site-footer{left:0;top:4392px;width:1200px;height:314px}
.foot-col{position:absolute;top:46px}
.foot-col h4{font-size:16px;font-weight:500;color:var(--ink);margin-bottom:18px}
.foot-col li{list-style:none;font-size:12px;line-height:22px;color:var(--grey);font-weight:300}
.contact-row{display:flex;gap:14px;margin-bottom:16px;font-size:12px;line-height:17px;color:var(--grey);font-weight:300}
.copyright{left:175px;top:262px;font-size:12px;color:var(--grey)}
.socials{left:946px;top:260px;display:flex;gap:6px}
.socials span{width:22px;height:22px;border-radius:50%;background:var(--teal)}
</style>
</head>
<body>

<header class="site-header">
  <div class="abs phone">
    <svg width="20" height="20" viewBox="0 0 24 24" fill="none" stroke="#0f4d9e" stroke-width="2.2"><path d="M5 3h4l2 5-3 2a12 12 0 0 0 6 6l2-3 5 2v4a2 2 0 0 1-2 2A18 18 0 0 1 3 5a2 2 0 0 1 2-2z"/></svg>
    <span>Phone:(010) 555 0142</span>
  </div>
  <div class="abs brand"><span class="brand-dot"></span>LUMORA</div>
  <a class="btn btn--navy" style="left:754px;width:141px">Book home visit</a>
  <a class="btn btn--teal" style="left:908px;width:116px">Book Nurses</a>
  <nav class="abs main-nav">
    <span class="active" style="left:203px">Home</span>
    <span style="left:294px">Services</span>
    <span style="left:413px">IV Therapies</span>
    <span style="left:551px">Booster Shots</span>
    <span style="left:677px">Genetics</span>
    <span style="left:776px">MyCare</span>
    <span style="left:878px">Locations</span>
  </nav>
  <div class="abs header-icons">
    <svg width="22" height="22" viewBox="0 0 24 24" fill="none" stroke="#333" stroke-width="1.8"><circle cx="12" cy="8" r="4.5"/><path d="M3 22c1-5 5-7 9-7s8 2 9 7"/></svg>
    <svg width="24" height="24" viewBox="0 0 24 24" fill="none" stroke="#333" stroke-width="1.8"><path d="M3 8h18l-2 12H5z"/><path d="M8 12c1 3 7 3 8 0"/></svg>
    <span class="cart-badge"></span>
  </div>
</header>

<section class="abs hero">
  <div class="abs hero-visual" role="img" aria-label="Glowing cyan DNA double helix rising diagonally over a dark blue molecular network"></div>
  <h1 class="abs hero-title">Lumora</h1>
  <p class="abs hero-sub">Sed ut perspiciatis unde omnis iste<br>natus error sit voluptatantium</p>
  <a class="btn btn--teal">Book Appointment</a>
</section>

<section class="services">
  <h2 class="section-title" style="top:830px">Our Services</h2>

  <div class="service-card tone-a" role="img" aria-label="Clinician taking a blood sample" style="left:172px;top:908px">
    <svg width="60" height="60" viewBox="0 0 60 60" fill="none" stroke="#fff" stroke-width="2.5"><rect x="8" y="6" width="12" height="4"/><path d="M10 10v34a4 4 0 0 0 8 0V10"/><rect x="24" y="6" width="12" height="4"/><path d="M26 10v34a4 4 0 0 0 8 0V10"/><path d="M48 24c-6 8-8 11-8 15a8 8 0 0 0 16 0c0-4-2-7-8-15z"/><path d="M44 39h8M48 35v8"/></svg>
    <div class="service-label">Blood Testing</div>
  </div>
  <div class="service-card tone-b" role="img" aria-label="Technician at a laboratory computer" style="left:389px;top:908px">
    <svg width="60" height="60" viewBox="0 0 60 60" fill="none" stroke="#fff" stroke-width="2.5"><rect x="8" y="12" width="44" height="28" rx="2"/><path d="M4 46h52"/><circle cx="22" cy="26" r="6"/><path d="M22 20v6h6M34 32v-6M40 32v-10M46 32v-4"/></svg>
    <div class="service-label">Laboratory analysis</div>
  </div>
  <div class="service-card tone-c" role="img" aria-label="Patient receiving an IV drip" style="left:606px;top:908px">
    <svg width="60" height="60" viewBox="0 0 60 60" fill="none" stroke="#fff" stroke-width="2.5"><path d="M18 6h20v20a10 10 0 0 1-20 0z"/><path d="M28 36v8M22 14h10M22 20h8"/><path d="M28 44c0 8 12 8 14 2"/><circle cx="46" cy="46" r="4"/></svg>
    <div class="service-label">IV therapy</div>
  </div>
  <div class="service-card tone-a" role="img" aria-label="Nurse preparing an infusion drip" style="left:824px;top:908px">
    <svg width="60" height="60" viewBox="0 0 60 60" fill="none" stroke="#fff" stroke-width="2.5"><rect x="14" y="8" width="28" height="40" rx="3"/><rect x="22" y="4" width="12" height="8"/><path d="M28 18v12M22 24h12M20 38h16"/><path d="M46 20h6v22l-3 4-3-4z"/></svg>
    <div class="service-label">IV infusion drips</div>
  </div>

  <div class="service-card tone-c" role="img" aria-label="Phlebotomist at work in a clinic" style="left:172px;top:1156px">
    <svg width="60" height="60" viewBox="0 0 60 60" fill="none" stroke="#fff" stroke-width="2.5"><path d="M44 6l10 10M49 11L22 38l-8-8L41 3M18 34l-10 10M30 22l4 4M24 28l4 4M8 44l-4 12 12-4"/></svg>
    <div class="service-label">Phlebotomy services</div>
  </div>
  <div class="service-card tone-b" role="img" aria-label="Home care nurse visiting a patient" style="left:389px;top:1156px">
    <svg width="60" height="60" viewBox="0 0 60 60" fill="none" stroke="#fff" stroke-width="2.5"><path d="M8 28L30 8l22 20"/><path d="M14 24v28h32V24"/><path d="M30 28v16M22 36h16"/></svg>
    <div class="service-label">Nurses for Home<br>care services</div>
  </div>
  <div class="service-card tone-a" role="img" aria-label="Patient being prepared for international travel" style="left:606px;top:1156px">
    <svg width="60" height="60" viewBox="0 0 60 60" fill="none" stroke="#fff" stroke-width="2.5"><circle cx="30" cy="30" r="24"/><ellipse cx="30" cy="30" rx="10" ry="24"/><path d="M6 30h48M10 18h40M10 42h40"/></svg>
    <div class="service-label">Patient repatriation<br>services to their<br>countries</div>
  </div>
  <div class="service-card tone-d" role="img" aria-label="Wheelchair and hospital beds in a ward" style="left:824px;top:1156px">
    <svg width="60" height="60" viewBox="0 0 60 60" fill="none" stroke="#fff" stroke-width="2.5"><circle cx="20" cy="8" r="4"/><path d="M20 14v18h18l6 14"/><circle cx="22" cy="40" r="14"/><circle cx="48" cy="50" r="4"/></svg>
    <div class="service-label">Hire of medical<br>equipments including<br>beds and wheelchairs</div>
  </div>
</section>

<section class="about">
  <div class="abs about-photo" role="img" aria-label="Nurse in blue gloves preparing a smiling client in a white robe for an IV vitamin infusion"></div>
  <div class="abs about-panel">
    <h2>About Lumora</h2>
    <p class="body-copy">Sed ut perspiciatis unde omnis iste natus error sit voluptate m accusantium doloremque laudantium, totam rem aperiam, eaque ipsa quae ab illo inventore veritatis et quasi architecto beatae vitae dicta sunt explicabo. Nemo enim ipsam voluptat em quia voluptas sit aspernatur aut odit aut fugit, sed quia consequuntur magni dolores eos qui ratione voluptatem seq ui nesciunt. Neque porro quisquam est, qui dolorem ipsum quia dolor sit amet, consectetur, adipisci velit, sed quia non numquam eius modi tempora incidunt ut labore et dolore magnam aliquam quaerat voluptatem.</p>
    <a class="btn btn--teal">Book nurse for international<br>Home care journey</a>
  </div>
</section>

<section class="supplements">
  <h2 class="section-title" style="top:2106px">Supplements</h2>
  <div class="supp" style="left:175px;top:2200px">
    <div class="supp-visual" role="img" aria-label="Syringe beside a vitamin vial" style="background:radial-gradient(ellipse 80px 60px at 70px 100px,#dfe3e8,transparent 70%),radial-gradient(ellipse 90px 30px at 120px 60px,#eef1f4,transparent 70%)"></div>
    <h3>Loremusom</h3>
    <p>Sed ut perspiciatis un<br>de omnis istnaturor sivolu<br>poteccusanti dolor</p>
  </div>
  <div class="supp" style="left:469px;top:2200px">
    <div class="supp-visual" role="img" aria-label="Amber and clear supplement vials" style="background:radial-gradient(ellipse 40px 60px at 60px 80px,#f0c878,transparent 75%),radial-gradient(ellipse 60px 66px at 135px 70px,#e3e7eb,transparent 75%)"></div>
    <h3>Loremusom</h3>
    <p>Sed ut perspiciatis un<br>de omnis istnaturor sivolu<br>poteccusanti dolor</p>
  </div>
  <div class="supp" style="left:761px;top:2200px">
    <div class="supp-visual" role="img" aria-label="Ampoule and vitamin vials" style="background:radial-gradient(ellipse 18px 66px at 40px 76px,#e6e9ec,transparent 80%),radial-gradient(ellipse 66px 62px at 125px 74px,#dde1e5,transparent 75%)"></div>
    <h3>Loremusom</h3>
    <p>Sed ut perspiciatis un<br>de omnis istnaturor sivolu<br>poteccusanti dolor</p>
  </div>
  <a class="btn btn--navy" style="left:504px;top:2560px;width:194px;height:40px;font-size:16px;font-weight:400">Select Treatment</a>
</section>

<section class="future">
  <div class="abs future-panel">
    <h2>A Future to<br>Believe in</h2>
    <p class="body-copy">Sed ut perspiciatis unde omnis iste natus error sit voluptate m accusantium doloremque laudantium, totam rem aperiam, eaque ipsa quae ab illo inventore veritatis et quasi architecto beatae vitae dicta sunt explicabo. Nemo enim ipsam voluptat em quia voluptas sit aspernatur aut odit aut fugit, sed quia consequuntur magni dolores eos qui ratione voluptatem seq ui nesciunt. Neque porro quisquam est, qui dolorem ipsum quia dolor sit amet, consectetur, adipisci velit, sed quia non numquam eius modi tempora incidunt</p>
    <a class="btn btn--teal">Book Appointment</a>
  </div>
  <div class="abs future-photo" role="img" aria-label="Doctor in a white coat holding a tablet with glowing molecular data overlays"></div>
</section>

<section class="vitamin">
  <svg class="abs hex" width="416" height="483" viewBox="0 0 416 483" role="img" aria-label="Blue DNA strand with a red glow inside a hexagon frame">
    <defs>
      <radialGradient id="hexGlow" cx="62%" cy="45%" r="70%">
        <stop offset="0" stop-color="#f06a7c"/>
        <stop offset="0.12" stop-color="#b04a78"/>
        <stop offset="0.32" stop-color="#2e6fb0"/>
        <stop offset="0.65" stop-color="#0c2c66"/>
        <stop offset="1" stop-color="#04163d"/>
      </radialGradient>
      <radialGradient id="hexCyan" cx="35%" cy="30%" r="45%">
        <stop offset="0" stop-color="#7fd6ff" stop-opacity=".55"/>
        <stop offset="1" stop-color="#7fd6ff" stop-opacity="0"/>
      </radialGradient>
    </defs>
    <polygon points="208,0 416,121 416,362 208,483 0,362 0,121" fill="url(#hexGlow)"/>
    <polygon points="208,0 416,121 416,362 208,483 0,362 0,121" fill="url(#hexCyan)"/>
  </svg>
  <h2>Vitamin Injections</h2>
  <p class="body-copy">Sed ut perspiciatis unde omnis iste natus error sit voluptate m accusantium doloremque laudantium, totam rem aperiam, eaque ipsa quae ab illo inventore veritatis et quasi architecto beatae vitae dicta sunt explicabo. Nemo enim ipsam voluptat em quia voluptas sit aspernatur aut odit aut fugit, sed quia consequuntur magni dolores eos qui ratione voluptatem seq ui nesciunt. Neque porro quisquam est, qui dolorem ipsum quia dolor sit amet, consectetur, adipisci velit, sed quia non numquam eius modi tempora incidunt</p>
  <a class="btn btn--teal">Book Now</a>
</section>

<section class="abs testimonials">
  <h2>Testimonials</h2>
  <article class="quote-card" style="left:126px">
    <svg width="28" height="20" viewBox="0 0 28 20" fill="#33b8a4"><path d="M0 20V11L6 0h5L7 10h5v10zM15 20V11l6-11h5l-4 10h5v10z"/></svg>
    <p>"Lorem ipsum dolor sit amet, consectet ur adipiscing elit, sed do eiusmod tempor incididunt ut labore et dolore magna aiq uaenim ad minim venia elited</p>
    <cite>- Mara Ellison</cite>
  </article>
  <article class="quote-card" style="left:426px">
    <svg width="28" height="20" viewBox="0 0 28 20" fill="#33b8a4"><path d="M0 20V11L6 0h5L7 10h5v10zM15 20V11l6-11h5l-4 10h5v10z"/></svg>
    <p>"Lorem ipsum dolor sit amet, consectet ur adipiscing elit, sed do eiusmod tempor incididunt ut labore et dolore magna aiq uaenim ad minim venia elited</p>
    <cite>- Mara Ellison</cite>
  </article>
  <article class="quote-card" style="left:761px">
    <svg width="28" height="20" viewBox="0 0 28 20" fill="#33b8a4"><path d="M0 20V11L6 0h5L7 10h5v10zM15 20V11l6-11h5l-4 10h5v10z"/></svg>
    <p>"Lorem ipsum dolor sit amet, consectet ur adipiscing elit, sed do eiusmod tempor incididunt ut labore et dolore magna aiq uaenim ad minim venia elited</p>
    <cite>- Mara Ellison</cite>
  </article>
</section>

<footer class="abs site-footer">
  <div class="foot-col" style="left:175px">
    <h4>Contact</h4>
    <div class="contact-row">
      <svg width="22" height="22" viewBox="0 0 24 24" fill="none" stroke="#555" stroke-width="1.6"><path d="M12 22s7-7 7-12a7 7 0 0 0-14 0c0 5 7 12 7 12z"/><circle cx="12" cy="10" r="2.5"/></svg>
      <span>412 Linden Row,<br>Harbor Vale, Westmere</span>
    </div>
    <div class="contact-row">
      <svg width="22" height="22" viewBox="0 0 24 24" fill="none" stroke="#555" stroke-width="1.6"><path d="M5 3h4l2 5-3 2a12 12 0 0 0 6 6l2-3 5 2v4a2 2 0 0 1-2 2A18 18 0 0 1 3 5a2 2 0 0 1 2-2z"/></svg>
      <span>8 800 555 014 22<br>8 800 555 017 36</span>
    </div>
    <div class="contact-row">
      <svg width="22" height="22" viewBox="0 0 24 24" fill="none" stroke="#555" stroke-width="1.6"><rect x="2" y="5" width="20" height="14"/><path d="M2 5l10 8 10-8"/></svg>
      <span>hello@lumoracare.com<br>care@lumoracare.com</span>
    </div>
  </div>
  <div class="foot-col" style="left:442px">
    <h4>Supplement</h4>
    <ul><li>Lorem ipsum dolo</li><li>Consectetur adipiscing elit.</li><li>Fusce eget leo tincid</li><li>Donec consequat</li><li>Praesent elementum</li><li>Mauris posuere</li></ul>
  </div>
  <div class="foot-col" style="left:681px">
    <h4>Company</h4>
    <ul><li>Lorem ipsum dolo</li><li>Consectetur adipiscing elit.</li><li>Fusce eget leo tincid</li><li>Donec consequat</li><li>Praesent elementum</li><li>Aenean a ex eu lectu</li></ul>
  </div>
  <div class="foot-col" style="left:911px">
    <h4>Other Links</h4>
    <ul><li>Lorem ipsum dolo</li><li>Consectetur adeli</li><li>Fusce eget leo tincid</li><li>Donec consequat</li><li>Praesent elementum</li><li>Aenean a ex eu lectu</li></ul>
  </div>
  <p class="abs copyright">Copyright 2020 All Rights Reserved</p>
  <div class="abs socials"><span></span><span></span><span></span></div>
</footer>

</body>
</html>
```